TK Homes - Stone Dorf Design

Looking for a double sides design, 1 side for my realestate and the other for home building. ( TK Homes on 1 side, Stone Dorf card on the other Side
Side 1 - Marek Tove ~ Vox Realty logo and Company ( the Property quarter )
Marek Tove
Marek@Marektove.example
IG - Marek_Bzq_Realtor
FB - marekt
Cell - 5558130467
3847 61 St Nw

Side 2
Marek Tove
5558130467
IG - Stonedorf_Bzq
Stonedorfdev@mailbox.example

Target Market(s)

Home buyers/ sellers

Industry/Entity Type

Home builders - Realestate

Contact Information for Business Card

Above

Requirements
Must have
• Black OR White background - my information -

```html
<!DOCTYPE html>
<html lang="en">
<head>
<meta charset="utf-8">
<title>TK Homes – Stone Dorf Design business cards</title>
<link href="https://fonts.googleapis.com/css2?family=Cinzel:wght@500&family=Tinos&display=swap" rel="stylesheet">
<style>
  :root {
    --backdrop: #161617;
    --card: #1d1d1e;
    --blue: #1b75bc;
    --white: #f2f2f2;
    --muted: #8a8a8a;
    --accent-red: #d9263f;
  }
  * { margin: 0; padding: 0; box-sizing: border-box; }
  html, body { width: 1200px; height: 1059px; overflow: hidden; }
  body { background: var(--backdrop); position: relative; }

  .card {
    position: absolute;
    background: var(--card);
    border-radius: 18px;
    box-shadow: 0 10px 24px rgba(0,0,0,.55);
  }
  .card--realty { left: 257px; top: 89px; width: 687px; height: 390px; }
  .card--builder { left: 254px; top: 546px; width: 693px; height: 394px; }

  .divider { position: absolute; width: 1px; background: var(--blue); }
  .card--realty .divider { left: 343px; top: 102px; height: 188px; }
  .card--builder .divider { left: 346px; top: 126px; height: 145px; }

  .brand-mark {
    position: absolute;
    font-family: "Cinzel", serif;
    font-weight: 500;
    white-space: nowrap;
    transform: translateX(-50%);
    display: flex; align-items: center; gap: 10px;
  }
  .card--realty .brand-mark { left: 196px; top: 196px; font-size: 40px; color: var(--blue); }
  .card--builder .brand-mark { left: 193px; top: 196px; font-size: 42px; color: var(--white); }
  .brand-mark .dot { width: 12px; height: 12px; background: currentColor; }

  .holder-name {
    position: absolute;
    font-family: "Cinzel", serif;
    font-weight: 500;
    color: var(--white);
    font-size: 34px;
    white-space: nowrap;
  }
  .card--realty .holder-name { left: 374px; top: 92px; }
  .card--builder .holder-name { left: 377px; top: 106px; }

  .contact-list { position: absolute; list-style: none; font-family: "Tinos", serif; color: var(--white); }
  .card--realty .contact-list { left: 379px; top: 155px; font-size: 18.5px; line-height: 23.3px; }
  .card--builder .contact-list { left: 379px; top: 171px; font-size: 19.5px; line-height: 26.5px; }
  .contact-list li { display: flex; align-items: center; gap: 8px; white-space: nowrap; }
  .contact-list svg { width: 12px; height: 12px; flex: none; fill: var(--blue); }

  .partner-badge { position: absolute; }
  .partner-badge--quarter { left: 509px; top: 329px; width: 85px; height: 32px; background: var(--white); border-top: 6px solid var(--accent-red); }
  .partner-badge--vox { left: 611px; top: 327px; width: 48px; height: 34px; border: 2px solid var(--white); border-radius: 17px; }
</style>
</head>
<body>

<section class="card card--realty" aria-label="Real estate side">
  <div class="brand-mark"><span class="dot"></span>Marek Tove</div>
  <div class="divider"></div>
  <h1 class="holder-name">Marek Tove</h1>
  <ul class="contact-list">
    <li><svg viewBox="0 0 12 12"><path d="M2 1l2.5 0 1 3-1.5 1a7 7 0 0 0 3 3l1-1.5 3 1V11a1 1 0 0 1-1 1A10 10 0 0 1 1 2a1 1 0 0 1 1-1z"/></svg>5558130467</li>
    <li><svg viewBox="0 0 12 12"><path d="M0 5l6-4 6 4v6H0z M1.5 5.5l4.5 3 4.5-3"/></svg>Marek@Marektove.example</li>
    <li><svg viewBox="0 0 12 12"><circle cx="6" cy="6" r="6"/></svg>www.Marektove.example</li>
    <li><svg viewBox="0 0 12 12"><path d="M6 0a4.5 4.5 0 0 1 4.5 4.5C10.5 8 6 12 6 12S1.5 8 1.5 4.5A4.5 4.5 0 0 1 6 0zm0 3a1.5 1.5 0 1 0 0 3 1.5 1.5 0 0 0 0-3z"/></svg>3847 61 St Nw</li>
    <li><svg viewBox="0 0 12 12"><circle cx="6" cy="6" r="5"/></svg>Marek_Bzq_Realtor</li>
    <li><svg viewBox="0 0 12 12"><circle cx="6" cy="6" r="5"/></svg>marekt</li>
  </ul>
  <div class="partner-badge partner-badge--quarter" role="img" aria-label="The Property Quarter partner badge"></div>
  <div class="partner-badge partner-badge--vox" role="img" aria-label="Vox Realty partner badge"></div>
</section>

<section class="card card--builder" aria-label="Home building side">
  <div class="brand-mark"><span class="dot"></span>Stone Dorf</div>
  <div class="divider"></div>
  <h2 class="holder-name">Marek Tove</h2>
  <ul class="contact-list">
    <li><svg viewBox="0 0 12 12"><path d="M2 1l2.5 0 1 3-1.5 1a7 7 0 0 0 3 3l1-1.5 3 1V11a1 1 0 0 1-1 1A10 10 0 0 1 1 2a1 1 0 0 1 1-1z"/></svg>5558130467</li>
    <li><svg viewBox="0 0 12 12"><path d="M0 5l6-4 6 4v6H0z"/></svg>Stonedorfdev@mailbox.example</li>
    <li><svg viewBox="0 0 12 12"><circle cx="6" cy="6" r="6"/></svg>www.stonedorfdev.example</li>
    <li><svg viewBox="0 0 12 12"><circle cx="6" cy="6" r="5"/></svg>Stonedorf_Bzq</li>
  </ul>
</section>

</body>
</html>
```